Brell Stone Company Business Cards

Front and Back Business Card - logo and text setup - cool design. I need workable photoshop or illustrator files so I can setup each employee card with design that is created
Updates

Hi everyone, thank you for the great entries. Please no more white and blue cards - there are so many already - black and silver only now please. thanks!

Target Market(s)

Construction Industry - Facility Managers

Industry/Entity Type

Construction

Contact Information for Business Card

I really like contemporary simplistic looks - clean neat....not opposed to seeing some black backrounds

Requirements
Must have
• Logo/website address with design on front only - www.brellstone-example.com (logo attached)
• Back:
• Name/Title/Company Address/Phone/email address
Nice to have
• Cool design
Should not have
• Nothing gimmicky like Fire or Water - since we are a Fire Protection company - it has all been done

```html
<!DOCTYPE html>
<html lang="en">
<head>
<meta charset="utf-8">
<title>Brell Stone Company – Business Cards</title>
<link href="https://fonts.googleapis.com/css2?family=Work+Sans:wght@400;500;700&display=swap" rel="stylesheet">
<style>
  :root {
    --stage: #141414;
    --card: #222222;
    --silver: #c9ccd1;
    --silver-light: #eceef1;
    --silver-dark: #8a8e94;
    --text: #eeeeee;
    --muted: #d2d4d7;
  }
  * { margin: 0; padding: 0; box-sizing: border-box; }
  html, body { width: 1200px; height: 900px; overflow: hidden; background: var(--stage); }
  body { font-family: "Work Sans", Arial, sans-serif; color: var(--text); }
  .card {
    position: absolute;
    left: 250px;
    width: 700px;
    height: 400px;
    background: var(--card);
    overflow: hidden;
  }
  .card--front { top: 35px; }
  .card--back { top: 465px; }
  .dash-band { position: absolute; left: 0; bottom: 14px; width: 700px; height: 10px; }
  .brand-name {
    font-family: "Work Sans", Arial, sans-serif;
    font-weight: 700;
    color: var(--silver);
    letter-spacing: 0.5px;
    white-space: nowrap;
  }
  .card--front .brand-name {
    position: absolute;
    top: 150px; left: 0; width: 100%;
    text-align: center;
    font-size: 54px;
  }
  .front-web {
    position: absolute;
    top: 232px; left: 0; width: 100%;
    text-align: center;
    font-size: 17px;
    letter-spacing: 2px;
    color: var(--muted);
  }
  .card--back .brand-name {
    position: absolute;
    top: 42px; left: 40px;
    font-size: 38px;
  }
  .divider {
    position: absolute;
    left: 40px; top: 250px;
    width: 590px; height: 2px;
    background: var(--silver);
  }
  .holder { position: absolute; right: 70px; top: 190px; text-align: right; }
  .holder-name { font-size: 27px; font-weight: 500; color: var(--silver-light); letter-spacing: 1.5px; }
  .holder-title { font-size: 16px; color: var(--muted); letter-spacing: 1px; margin-top: 2px; }
  .edge-mark { position: absolute; right: 0; top: 196px; width: 18px; height: 48px; background: var(--silver); }
  .contact-list { position: absolute; left: 40px; top: 266px; list-style: none; }
  .contact-list li { display: flex; align-items: center; font-size: 16px; letter-spacing: 1px; height: 24px; color: var(--muted); }
  .contact-list svg { width: 13px; height: 13px; margin-right: 12px; flex: none; }
  .address { position: absolute; right: 70px; top: 300px; text-align: right; font-size: 17px; line-height: 25px; letter-spacing: 1px; color: var(--muted); }
</style>
</head>
<body>
  <svg width="0" height="0" style="position:absolute">
    <defs>
      <linearGradient id="dash-fade" x1="0" y1="0" x2="700" y2="0" gradientUnits="userSpaceOnUse">
        <stop offset="0" stop-color="#f2f3f5"/>
        <stop offset="1" stop-color="#8a8e94"/>
      </linearGradient>
      <g id="dash-row" fill="url(#dash-fade)">
        <rect x="0" y="0" width="36" height="10"/>
        <rect x="60" y="0" width="40" height="10"/>
        <rect x="124" y="0" width="40" height="10"/>
        <rect x="188" y="0" width="40" height="10"/>
        <rect x="252" y="0" width="40" height="10"/>
        <rect x="316" y="0" width="40" height="10"/>
        <rect x="380" y="0" width="40" height="10"/>
        <rect x="444" y="0" width="40" height="10"/>
        <rect x="508" y="0" width="40" height="10"/>
        <rect x="572" y="0" width="40" height="10"/>
        <rect x="636" y="0" width="40" height="10"/>
        <rect x="690" y="0" width="10" height="10"/>
      </g>
    </defs>
  </svg>

  <section class="card card--front" aria-label="Card front">
    <div class="brand-name">Brell Stone</div>
    <div class="front-web">www.brellstone-example.com</div>
    <svg class="dash-band" viewBox="0 0 700 10"><use href="#dash-row"/></svg>
  </section>

  <section class="card card--back" aria-label="Card back">
    <div class="brand-name">Brell Stone</div>

    <div class="holder">
      <div class="holder-name">DANA WHITLOW</div>
      <div class="holder-title">Director</div>
    </div>
    <div class="edge-mark"></div>
    <div class="divider"></div>

    <ul class="contact-list">
      <li>
        <svg viewBox="0 0 16 16" aria-hidden="true"><path d="M4 1l3 3-2 2c1 2 3 4 5 5l2-2 3 3-2 2C7 14 2 9 2 3z" fill="var(--silver)"/></svg>
        (555) 014-2869
      </li>
      <li>
        <svg viewBox="0 0 16 16" aria-hidden="true"><rect x="4" y="1" width="8" height="4" fill="var(--silver)"/><rect x="1" y="6" width="14" height="6" rx="1" fill="var(--silver)"/><rect x="4" y="10" width="8" height="5" fill="var(--silver)"/></svg>
        (555) 014-2866
      </li>
      <li>
        <svg viewBox="0 0 16 16" aria-hidden="true"><rect x="1.5" y="3.5" width="13" height="9" fill="none" stroke="var(--silver)" stroke-width="1.5"/><path d="M1.5 3.5L8 9l6.5-5.5" fill="none" stroke="var(--silver)" stroke-width="1.5"/></svg>
        info@brellstone-example.com
      </li>
      <li>
        <svg viewBox="0 0 16 16" aria-hidden="true"><g fill="none" stroke="var(--silver)" stroke-width="1.3"><circle cx="8" cy="8" r="6.5"/><ellipse cx="8" cy="8" rx="3" ry="6.5"/><path d="M1.5 8h13"/></g></svg>
        www.brellstone-example.com
      </li>
    </ul>

    <div class="address">
      12-4 Harbor Works Drive<br>
      Eastwick, NY 11790
    </div>

    <svg class="dash-band" viewBox="0 0 700 10"><use href="#dash-row"/></svg>
  </section>
</body>
</html>
```